New Company Business Card design

Looking for a corporate looking business card utilising my new logo design - the logo i would like embossed as one option and flat as another - simplistic but stylish - less is more - we are an import export business launching into the market - i would like a couple of options as main background - Grey or Black

```html
<!DOCTYPE html>
<html lang="en">
<head>
<meta charset="utf-8">
<title>Meridian Trade Partners – Business Card</title>
<link href="https://fonts.googleapis.com/css2?family=Roboto:wght@300;400;500&display=swap" rel="stylesheet">
<style>
  :root {
    --backdrop: #262626;
    --card-light: #f2f2f2;
    --card-dark: #6a6a6a;
    --brand-blue: #2a7fcf;
    --text-grey: #555555;
    --text-white: #f4f4f4;
  }
  * { margin: 0; padding: 0; box-sizing: border-box; }
  html, body { width: 1200px; height: 799px; overflow: hidden; }
  body {
    background: var(--backdrop);
    font-family: "Roboto", Arial, sans-serif;
    position: relative;
  }
  .card {
    position: absolute;
    top: 251px;
    width: 520px;
    height: 297px;
    border-radius: 3px;
  }
  .card--front { left: 60px; background: var(--card-light); }
  .card--back { left: 620px; background: var(--card-dark); }

  .contact { position: absolute; left: 40px; top: 36px; color: var(--text-grey); }
  .contact__name {
    color: var(--brand-blue);
    font-size: 22px;
    font-weight: 400;
    letter-spacing: 0.5px;
    line-height: 1.1;
  }
  .contact__role { font-size: 13px; font-weight: 300; letter-spacing: 0.5px; margin-bottom: 8px; }
  .contact__address { font-size: 13px; line-height: 1.4; margin-bottom: 6px; }
  .contact__list { list-style: none; font-size: 13px; line-height: 1.45; }
  .contact__list li { display: flex; align-items: center; gap: 8px; }
  .contact__icon { width: 11px; height: 11px; flex: none; }
  .contact__icon * { fill: var(--brand-blue); }

  .brand-mark {
    position: absolute;
    display: flex;
    align-items: center;
    gap: 10px;
    color: var(--brand-blue);
    font-weight: 500;
  }
  .card--front .brand-mark { right: 34px; bottom: 40px; font-size: 17px; }
  .card--back .brand-mark {
    left: 50%; top: 42%;
    transform: translate(-50%, -50%);
    font-size: 28px;
    white-space: nowrap;
  }
  .brand-mark__dot { border-radius: 50%; background: var(--brand-blue); flex: none; }
  .card--front .brand-mark__dot { width: 18px; height: 18px; }
  .card--back .brand-mark__dot { width: 28px; height: 28px; }

  .web-address {
    position: absolute;
    left: 0; right: 0; bottom: 46px;
    text-align: center;
    color: var(--text-white);
    font-size: 13px;
    font-weight: 300;
    letter-spacing: 3px;
  }
</style>
</head>
<body>
  <section class="card card--front">
    <div class="contact">
      <h1 class="contact__name">DANIEL REYES</h1>
      <p class="contact__role">CEO/FOUNDER</p>
      <p class="contact__address">2140 Harbor View Road<br>Juneau, Alaska 99801</p>
      <ul class="contact__list">
        <li>
          <svg class="contact__icon" viewBox="0 0 12 12"><path d="M2.5 0.5 L4.5 0.5 L5 3.5 L3.6 4.4 Q4.8 7 7.6 8.4 L8.5 7 L11.5 7.5 L11.5 9.5 Q11.5 11.5 9.5 11.5 Q0.5 10.5 0.5 2.5 Q0.5 0.5 2.5 0.5 Z"/></svg>
          555 210 4837
        </li>
        <li>
          <svg class="contact__icon" viewBox="0 0 12 12"><rect x="3" y="0" width="6" height="12" rx="1"/></svg>
          555 384 9261
        </li>
        <li>
          <svg class="contact__icon" viewBox="0 0 12 12"><rect x="0" y="2" width="12" height="8" rx="1"/></svg>
          555 762 1308
        </li>
        <li>
          <svg class="contact__icon" viewBox="0 0 12 12"><path d="M0 2 H12 V10 H0 Z M0.8 2.6 L6 6.5 L11.2 2.6" style="fill:none;stroke:var(--brand-blue);stroke-width:1.2"/></svg>
          hello@meridiantrade.com
        </li>
        <li>
          <svg class="contact__icon" viewBox="0 0 12 12"><circle cx="6" cy="6" r="6"/></svg>
          www.meridiantrade.com
        </li>
      </ul>
    </div>
    <div class="brand-mark">
      <span class="brand-mark__dot"></span>
      <span class="brand-mark__name">Meridian Trade Partners</span>
    </div>
  </section>

  <section class="card card--back">
    <div class="brand-mark">
      <span class="brand-mark__dot"></span>
      <span class="brand-mark__name">Meridian Trade Partners</span>
    </div>
    <p class="web-address">www.meridiantradepartners.com</p>
  </section>
</body>
</html>
```